Book Title: “Faith: Road of Endless Grace” Please see the attachment “Text on the cover”.

Book Cover Design Instructions: This book is meant for people of all religions and nationalities. Therefore, on the cover, there should be no mosque or an object specific to any religion. The primary emphasis should be on the "unconditional love of God." Therefore, use universal symbols of love. The second priority themes could be Sufism, Peace, and self-improvement. Rest is your imagination. Please also see the attachment: 'Book description and author's Bio.'
This book has the potential to be a best seller. Please do a good job.
What Book Cover Formats are required: A designer should submit cover designs in three formats: (1) eBook, (2) Paperback, and (3) Hardback. These books will be published on Borvex QPL.
Format requirements for eBooks are available from: https://qpl.borvex.example/en_US/help/topic/R731928457.
You can find paperback and hardback cover measurements from: https://qpl.borvex.example/en_US/cover-calculator
• To complete the project, all three formats should be accepted by Borvex QPL.
• The book interior trim size is 6.14 X 9.21 inches.
• Interior Type: Premium color.
• No bleed.
• I do not upload barcode. So, the back cover should have room for Borvex to print the barcode.
• Number of pages 126.
Compensation for the designer: After selecting one designer, I will increase the amount by $200 on Artvelle to compensate for three deliverables.
Follow-up of the Project:
After the book is published, I may need minor revisions. For example, the number of pages may change. Therefore, I will need the same design in revised sizes. In that case, I will pay $25 for each revision. For example, if the number of pages changes, I will need a different spine for paperback and hardback, then I will pay the artist $25 + $25 = $50 for both designs.
List of Enclosers:
1. Text on the cover.
2. Book description and author's Bio for the back cover.
3. Later, I will upload my picture for the book's back cover.

Target Market(s)

Any adult

Industry/Entity Type

Any industry

Requirements
Must have
• Three Deliverables

```html
<!DOCTYPE html>
<html lang="en">
<head>
<meta charset="utf-8">
<title>Faith: Road of Endless Grace — Book Cover</title>
<link rel="stylesheet" href="https://fonts.googleapis.com/css2?family=Bebas+Neue&family=Montserrat:wght@500;600&display=swap">
<style>
  :root {
    --page-bg: #ffffff;
    --cover-top: #d95d1c;
    --cover-mid: #b84208;
    --cover-low: #a83400;
    --glow-core: #fff4c8;
    --glow-warm: #f59a1a;
    --glow-deep: #cf4a06;
    --shadow-dark: #1a0402;
    --ink-light: #ffffff;
  }
  * { margin: 0; padding: 0; box-sizing: border-box; }
  html, body {
    width: 1200px;
    height: 1200px;
    overflow: hidden;
    background: var(--page-bg);
  }
  .canvas {
    position: relative;
    width: 1200px;
    height: 1200px;
  }
  .book-cover {
    position: absolute;
    left: 295px;
    top: 141px;
    width: 618px;
    height: 925px;
    overflow: hidden;
    background: linear-gradient(180deg, var(--cover-top) 0%, var(--cover-mid) 35%, var(--cover-low) 70%, var(--cover-low) 100%);
  }
  .cover-art {
    position: absolute;
    left: 0;
    top: 619px;
    width: 618px;
    height: 306px;
    background:
      radial-gradient(ellipse 70px 60px at 303px 134px, var(--glow-core) 0%, var(--glow-warm) 45%, transparent 100%),
      radial-gradient(ellipse 220px 160px at 303px 150px, var(--glow-deep) 0%, transparent 100%),
      linear-gradient(180deg, rgba(26,4,2,0) 0%, rgba(26,4,2,0.55) 55%, var(--shadow-dark) 100%);
  }
  .cover-type {
    position: absolute;
    left: 0;
    top: 0;
    width: 618px;
    height: 925px;
  }
  .kicker, .tagline, .author {
    font-family: "Montserrat", Arial, sans-serif;
    font-weight: 500;
    fill: var(--ink-light);
    letter-spacing: 1.5px;
  }
  .title-line {
    font-family: "Bebas Neue", "Oswald", sans-serif;
    fill: var(--ink-light);
  }
</style>
</head>
<body>
  <main class="canvas">
    <section class="book-cover" aria-label="Book cover: Faith: Road of Endless Grace">
      <div class="cover-art" role="img" aria-label="Silhouetted hands forming a heart shape around a glowing setting sun"></div>
      <svg class="cover-type" viewBox="0 0 618 925" xmlns="http://www.w3.org/2000/svg">
        <text class="kicker" x="309" y="37" text-anchor="middle" font-size="25" textLength="450" lengthAdjust="spacingAndGlyphs">UNCONDITIONAL LOVE OF GOD</text>

        <text class="title-line" x="41" y="250" font-size="289" textLength="535" lengthAdjust="spacingAndGlyphs">FAITH</text>
        <text class="title-line" x="42" y="425" font-size="216" textLength="533" lengthAdjust="spacingAndGlyphs">ROAD OF</text>
        <text class="title-line" x="39" y="537" font-size="127" textLength="535" lengthAdjust="spacingAndGlyphs">ENDLESS GRACE</text>

        <text class="tagline" x="309" y="574" text-anchor="middle" font-size="24" textLength="452" lengthAdjust="spacingAndGlyphs">GUIDE TO CULTIVATING INNER</text>
        <text class="tagline" x="309" y="606" text-anchor="middle" font-size="24" textLength="426" lengthAdjust="spacingAndGlyphs">PEACE AND MINDFUL LIVING</text>

        <text class="author" x="309" y="914" text-anchor="middle" font-size="26" textLength="326" lengthAdjust="spacingAndGlyphs">DR. NOURA VALENTI</text>
      </svg>
    </section>
  </main>
</body>
</html>
```